Pawn & Gun store business card design

Hello! We would like a new business card design for our pawn & gun store. We loan money on items of value and sell firearms, jewelry, electronics & more.

Card will need to have the following information:

Business name - Prairie Nickel Pawn & Gun
Address - 2417 Hwy 53 S. Suite C Ashford Springs, OK 75246
Employees name - Darren Kellum
Phone number - 580-613-8840
Email - PrairieNickelPawn@Mailvera.com
Website - PrairieNickelPawn.com

Somewhere on the card we would like it to say "Offering 10 Month Layaway!" & "We buy & loan on anything of value!". Our main store color is orange (please see logo). Logo does not have to be on the business card but it can be. Would like the back to have an area to write a note on the back. We like vintage things like old coins, collectables, firearms and more so think about this in the design. We want a business card as unique as our store!

Colors

Designer to choose colors to be used in the design.

Requirements
Nice to have
• Vintage Style

```html
<!DOCTYPE html>
<html lang="en">
<head>
<meta charset="utf-8">
<title>Prairie Nickel Pawn &amp; Gun — Business Card</title>
<link rel="stylesheet" href="https://fonts.googleapis.com/css2?family=Libre+Baskerville:wght@400;700&family=Lato:wght@400&display=swap">
<style>
  :root {
    --stage: #2a2a2c;
    --card-dark: #1c1d1f;
    --card-light: #ffffff;
    --orange: #e0601c;
    --text-light: #f2f2f2;
    --rule-dark: #55575b;
    --rule-light: #cfcfcf;
    --faint: #f4ddd0;
  }
  * { box-sizing: border-box; margin: 0; padding: 0; }
  html, body { width: 1200px; height: 1108px; overflow: hidden; }
  body {
    background: var(--stage);
    display: flex;
    align-items: center;
    justify-content: center;
    gap: 80px;
  }
  .card {
    width: 440px;
    height: 770px;
    border-radius: 26px;
    position: relative;
    display: flex;
    flex-direction: column;
    align-items: center;
    text-align: center;
  }
  .card--front { background: var(--card-dark); color: var(--text-light); }
  .card--back { background: var(--card-light); }

  .brand-name {
    font-family: "Libre Baskerville", serif;
    font-weight: 700;
    color: var(--orange);
    text-transform: uppercase;
    line-height: 1.2;
    letter-spacing: 1px;
  }
  .card--front .brand-name { margin-top: 130px; font-size: 34px; width: 320px; }
  .card--back .brand-name { margin-top: 190px; font-size: 38px; width: 340px; color: var(--faint); }

  .person {
    font-family: "Libre Baskerville", serif;
    font-weight: 400;
    font-size: 29px;
    color: var(--orange);
    text-transform: uppercase;
    margin-top: 190px;
    letter-spacing: 0.5px;
  }
  .icon-rule {
    display: flex;
    align-items: center;
    width: 330px;
    gap: 8px;
    margin-top: 14px;
  }
  .icon-rule .line { flex: 1; height: 1px; background: var(--rule-dark); }
  .icon {
    width: 26px; height: 26px; border-radius: 50%;
    background: var(--orange);
    display: flex; align-items: center; justify-content: center;
  }
  .contact {
    font-family: "Lato", sans-serif;
    font-size: 20px;
    line-height: 1.3;
    margin-top: 8px;
  }
  .rule { width: 330px; height: 1px; background: var(--rule-dark); margin: 12px 0; }
  .address { font-family: "Lato", sans-serif; font-size: 20px; line-height: 1.3; }

  .back-rule { width: 330px; height: 1px; background: var(--rule-light); margin-top: 170px; }
  .offer {
    font-family: "Libre Baskerville", serif;
    font-weight: 700;
    font-size: 19px;
    color: var(--orange);
    text-transform: uppercase;
    line-height: 1.3;
  }
  .offer--layaway { margin-top: 22px; }
  .offer--buy { margin-top: 24px; }
</style>
</head>
<body>
  <section class="card card--front" aria-label="Card front">
    <h1 class="brand-name">Prairie Nickel Pawn &amp; Gun</h1>
    <p class="person">Darren Kellum</p>
    <div class="icon-rule">
      <span class="line"></span>
      <span class="icon" aria-label="Phone">
        <svg width="14" height="14" viewBox="0 0 24 24"><path fill="#fff" d="M6.6 10.8a15 15 0 0 0 6.6 6.6l2.2-2.2a1 1 0 0 1 1-.25 11.4 11.4 0 0 0 3.6.57 1 1 0 0 1 1 1V20a1 1 0 0 1-1 1A17 17 0 0 1 3 4a1 1 0 0 1 1-1h3.5a1 1 0 0 1 1 1c0 1.25.2 2.45.57 3.6a1 1 0 0 1-.25 1z"/></svg>
      </span>
      <span class="icon" aria-label="Email">
        <svg width="14" height="14" viewBox="0 0 24 24"><rect x="3" y="6" width="18" height="12" fill="#fff"/><path d="M3 6l9 7 9-7" fill="none" stroke="#e0601c" stroke-width="1.8"/></svg>
      </span>
      <span class="icon" aria-label="Website">
        <svg width="14" height="14" viewBox="0 0 24 24"><circle cx="12" cy="12" r="8" fill="none" stroke="#fff" stroke-width="2"/><path d="M4 12h16M12 4c3 3 3 13 0 16M12 4c-3 3-3 13 0 16" fill="none" stroke="#fff" stroke-width="1.5"/></svg>
      </span>
      <span class="line"></span>
    </div>
    <p class="contact">580-613-8840<br>PrairieNickelPawn@Mailvera.com<br>PrairieNickelPawn.com</p>
    <div class="rule"></div>
    <p class="address">2417 Hwy 53 S. Suite C<br>Ashford Springs, OK 75246</p>
  </section>

  <section class="card card--back" aria-label="Card back">
    <p class="brand-name" aria-hidden="true">Prairie Nickel Pawn &amp; Gun</p>
    <div class="back-rule"></div>
    <p class="offer offer--layaway">Offering 10 Month Layaway!</p>
    <p class="offer offer--buy">We Buy &amp; Loan On<br>Anything of Value!</p>
  </section>
</body>
</html>
```